Graphic Design for a 3 Banner Tradeshow Setup

We are a Pipe Restoration company that specializes in trenchless pipelining. We need a design for a 3 banner setup to use at tradeshows. See attached "banner specs" for sizing - note the 48" x 92" will be in between the two 36" x 92" banners. See attached "Mock-Up" of information each banner needs and utilize the color scheme of the banners we already have in the "both DWM banners" AI file attached. The final designs should communicate what we do and attract people into our booth. We would like to have graphics of realistic pipes for a before (dirty pipe), after cleaning pipe, and lined pipe - see example of "pipe pictures" attached. I'm not sure if this is something you can generate or if we will need to find images of our own to send. Also, see attached "screenshot-process" to see similar images we would like to use to showcase the process.
Target Market(s)
Homeowners, Property Managers, HOA Communities, Healthcare Facilities & Hospitals, and commercial properties
Industry/Entity Type
Trenchless Pipelining
Look and feel

```html
<!DOCTYPE html>
<html lang="en">
<head>
<meta charset="utf-8">
<title>DWM Tradeshow Banners</title>
<link href="https://fonts.googleapis.com/css2?family=Russo+One&family=Barlow:wght@500;700&family=Barlow+Condensed:wght@700&display=swap" rel="stylesheet">
<style>
:root{
  --stage:#bdbdbb;
  --navy:#0d1628;
  --deep:#0f2d6b;
  --blue:#1a63b8;
  --sky:#1ba7e6;
  --ice:#e8f3fb;
  --ink:#0b1324;
  --white:#ffffff;
}
*{margin:0;padding:0;box-sizing:border-box}
html,body{width:1200px;height:943px;overflow:hidden;background:var(--stage)}
.stage{position:relative;width:1200px;height:943px}
.banner{position:absolute;top:77px;height:788px;overflow:hidden;box-shadow:0 4px 14px rgba(0,0,0,.25)}
.side{width:309px;background:linear-gradient(180deg,var(--navy) 0%,var(--navy) 35%,var(--blue) 75%,var(--sky) 100%)}
.left{left:61px}.right{left:825px}
.center{left:394px;width:412px;background:var(--white)}
.brand{position:absolute;top:38px;left:0;width:100%;display:flex;align-items:center;justify-content:center;gap:10px}
.brand-mark{width:38px;height:38px;background:var(--sky)}
.brand-name{font-family:"Russo One",sans-serif;font-size:50px;color:var(--white);letter-spacing:4px;line-height:1}
.photo{position:absolute;left:0;width:100%;bottom:0}
.panel{position:absolute;left:33px;width:247px;top:119px;height:516px;border-radius:18px;background:linear-gradient(160deg,#ffffff,var(--ice) 50%,#cfe6f6);border:2px solid var(--sky)}
.tab{position:absolute;top:113px;left:71px;width:174px;height:29px;background:linear-gradient(180deg,var(--blue),var(--deep));border-radius:0 0 16px 16px;color:var(--white);font-family:"Russo One",sans-serif;font-size:16px;display:flex;align-items:center;justify-content:center;letter-spacing:.5px}
.right .panel{left:28px;width:253px}
.right .tab{left:68px}
.tile{position:absolute;width:62px;height:62px;border-radius:5px;background:linear-gradient(180deg,var(--blue),var(--deep));display:flex;align-items:center;justify-content:center;box-shadow:0 2px 4px rgba(0,0,0,.3)}
.tile svg{width:40px;height:40px;stroke:var(--white);fill:none;stroke-width:2}
.assess-label{position:absolute;left:0;width:309px;text-align:center;font-family:"Russo One",sans-serif;font-size:16px;line-height:17px;color:var(--ink)}
.fix-label{position:absolute;left:123px;font-family:"Russo One",sans-serif;font-size:17px;line-height:19px;color:var(--ink);letter-spacing:.5px}
.headline{position:absolute;left:0;width:100%;text-align:center;font-family:"Russo One",sans-serif;background:linear-gradient(180deg,var(--deep),var(--blue) 60%,var(--sky));-webkit-background-clip:text;background-clip:text;color:transparent;line-height:1}
.headline.big{top:23px;font-size:78px;letter-spacing:2px}
.headline.sub{top:95px;font-size:38px}
.band{position:absolute;top:143px;left:0;width:100%;height:113px;background:linear-gradient(180deg,var(--sky),var(--blue) 55%,var(--deep));color:var(--white);text-align:center;font-family:"Barlow Condensed",sans-serif;text-shadow:0 1px 2px rgba(0,0,0,.4)}
.band .lead{margin-top:16px;font-size:18px;letter-spacing:.5px}
.band .main{font-size:28px;line-height:29px;margin-top:4px;letter-spacing:.5px}
.art{position:absolute;border-radius:6px}
.step-pipe{background:linear-gradient(135deg,#6b6f78,#a56a3c 45%,#3f4450)}
.lined-pipe{background:linear-gradient(135deg,#2c3038,#3aa0e0 50%,#1a5fae)}
.before-after{left:213px;top:309px;width:199px;height:232px;border-radius:50% 0 0 50%;overflow:hidden}
.before{height:50%;background:linear-gradient(160deg,#6a4a2a,#9b5e2d 50%,#3a2a1a);position:relative}
.after{height:50%;background:linear-gradient(180deg,#45b8ec,#1a6dbb 60%,#0f3f7d);position:relative}
.ba-label{position:absolute;left:48px;font-family:"Barlow",sans-serif;font-weight:700;font-size:12px;color:var(--white)}
.ring{position:absolute;left:95px;top:295px;width:320px;height:330px;border:5px solid #e2e4e8;border-radius:50%}
.num{position:absolute;width:29px;height:29px;border-radius:50%;background:linear-gradient(180deg,var(--sky),var(--deep));border:2px solid var(--white);box-shadow:0 1px 3px rgba(0,0,0,.4);color:var(--white);font-family:"Russo One",sans-serif;font-size:18px;display:flex;align-items:center;justify-content:center}
.caption{position:absolute;font-family:"Barlow",sans-serif;font-weight:500;font-size:9.5px;line-height:11px;color:var(--ink)}
.contact{position:absolute;left:18px;top:682px;width:376px;height:106px;background:linear-gradient(180deg,#000,#1a1c22);border-radius:14px 14px 0 0;text-align:center}
.cta{position:absolute;left:42px;top:671px;width:325px;height:28px;background:var(--sky);border-radius:3px;color:var(--white);font-family:"Barlow Condensed",sans-serif;font-size:15px;display:flex;align-items:center;justify-content:center;letter-spacing:.3px}
.web{margin-top:29px;font-family:"Russo One",sans-serif;font-size:18px;color:var(--sky);letter-spacing:1px}
.phone{margin-top:4px;font-family:"Russo One",sans-serif;font-size:27px;color:var(--white);letter-spacing:1px}
</style>
</head>
<body>
<div class="stage">

  <section class="banner side left">
    <div class="brand"><span class="brand-mark"></span><span class="brand-name">DWM</span></div>
    <div class="photo" role="img" aria-label="Photo of a technician in hi-vis clothing running a sewer inspection camera" style="top:563px;background:linear-gradient(160deg,#f08a2a,#a89a86 45%,#6d6a66 75%,#3c3a3a)"></div>
    <div class="panel"></div>
    <div class="tab">WE ASSESS</div>

    <div class="tile" style="left:125px;top:157px"><svg viewBox="0 0 40 40"><rect x="8" y="8" width="10" height="14" rx="2"/><path d="M13 22v10M24 8v22a4 4 0 0 0 8 0V8"/></svg></div>
    <div class="assess-label" style="top:224px">CCTV PIPE<br>INVESTIGATION</div>

    <div class="tile" style="left:125px;top:271px"><svg viewBox="0 0 40 40"><path d="M4 14h7l9 8 9-8h7M11 14l-3 10M29 14l3 10M14 24l6 5 6-5"/></svg></div>
    <div class="assess-label" style="top:340px">SCOPE<br>DEVELOPMENT</div>

    <div class="tile" style="left:125px;top:388px"><svg viewBox="0 0 40 40"><rect x="8" y="5" width="18" height="28" rx="2"/><rect x="11" y="8" width="12" height="5"/><path d="M11 18h3M16 18h3M11 23h3M16 23h3M11 28h3M16 28h3"/><circle cx="30" cy="24" r="6"/></svg></div>
    <div class="assess-label" style="top:457px">BUDGETARY<br>EVALUATION</div>

    <div class="tile" style="left:125px;top:507px"><svg viewBox="0 0 40 40"><circle cx="22" cy="16" r="9"/><path d="M22 7v18M16 23l-10 10"/><path d="M31 6v26"/></svg></div>
    <div class="assess-label" style="top:576px">PROJECT<br>OVERSIGHT</div>
  </section>

  <section class="banner center">
    <div class="headline big">PIPE</div>
    <div class="headline sub">PROBLEMS?</div>
    <div class="band">
      <div class="lead">WE HELP FIX PIPE PROBLEMS</div>
      <div class="main">WITHOUT HAVING TO<br>TEAR UP YOUR BUIDLING</div>
    </div>

    <div class="ring"></div>
    <div class="art step-pipe" role="img" aria-label="Cutaway of a corroded pipe with root intrusion" style="left:103px;top:270px;width:155px;height:94px"></div>
    <div class="art step-pipe" role="img" aria-label="Cutaway of a pipe being mechanically cleaned by a cutting tool" style="left:28px;top:395px;width:160px;height:80px"></div>
    <div class="art lined-pipe" role="img" aria-label="Cutaway of a CIPP liner being pulled into the pipe" style="left:50px;top:527px;width:155px;height:77px"></div>
    <div class="art lined-pipe" role="img" aria-label="Cutaway of finished lined pipe" style="left:238px;top:566px;width:135px;height:94px"></div>
    <div class="art before-after" role="img" aria-label="Photo of a pipe before and after restoration">
      <div class="before"><span class="ba-label" style="bottom:8px">BEFORE</span></div>
      <div class="after"><span class="ba-label" style="top:16px">AFTER</span></div>
    </div>

    <div class="num" style="left:242px;top:271px">1</div>
    <div class="caption" style="left:276px;top:273px;width:125px">A sewer camera is used to investigate the pipe to determine condition</div>
    <div class="num" style="left:118px;top:354px">2</div>
    <div class="caption" style="left:42px;top:348px;width:70px">The Pipe is mechanically cleaned</div>
    <div class="num" style="left:104px;top:481px">3</div>
    <div class="caption" style="left:20px;top:483px;width:82px">A CIPP Liner is pulled into place and the bladder inflated.</div>
    <div class="num" style="left:173px;top:587px">4</div>
    <div class="caption" style="left:95px;top:627px;width:130px">After curing the bladder is removed leaving behind a strictrial pipe within a pipe</div>

    <div class="contact">
      <div class="web">WWW.DWMPIPE.COM</div>
      <div class="phone">1-800-555-0142</div>
    </div>
    <div class="cta">CALL TODAY FOR ALL YOUR PIPE RESTORATION</div>
  </section>

  <section class="banner side right">
    <div class="brand"><span class="brand-mark"></span><span class="brand-name">DWM</span></div>
    <div class="photo" role="img" aria-label="Photo of hands tightening a chrome sink drain trap with a wrench" style="top:602px;background:linear-gradient(160deg,#9aa2aa,#e4e7ea 45%,#b8bec4 70%,#d8dcdf)"></div>
    <div class="panel"></div>
    <div class="tab">WE FIX</div>

    <div class="tile" style="left:49px;top:155px"><svg viewBox="0 0 40 40"><path d="M10 6v18a8 8 0 0 0 16 0v-6h8"/><path d="M16 6v18a2 2 0 0 0 4 0v-6"/></svg></div>
    <div class="fix-label" style="top:168px">SLOW<br>DRAINS</div>
    <div class="tile" style="left:49px;top:235px"><svg viewBox="0 0 40 40"><path d="M8 6v20M14 6v12h10a6 6 0 0 1 6 6v4"/><path d="M4 30h32M4 34h32"/></svg></div>
    <div class="fix-label" style="top:248px">WATER<br>BACK - UPS</div>
    <div class="tile" style="left:49px;top:315px"><svg viewBox="0 0 40 40"><path d="M12 6c-3 4 3 6 0 10M20 6c-3 4 3 6 0 10M28 6c-3 4 3 6 0 10"/><ellipse cx="20" cy="26" rx="14" ry="5"/><path d="M6 26v4a14 5 0 0 0 28 0v-4"/></svg></div>
    <div class="fix-label" style="top:328px">SEWER<br>ODORS</div>
    <div class="tile" style="left:49px;top:395px"><svg viewBox="0 0 40 40"><path d="M4 15h32M4 25h32M4 13v14M36 13v14M20 15l-2 5 3 2-2 3"/><path d="M20 28v6"/></svg></div>
    <div class="fix-label" style="top:408px">CRACKED<br>PIPES</div>
    <div class="tile" style="left:49px;top:475px"><svg viewBox="0 0 40 40"><path d="M4 22h32M4 32h32M20 22V8M20 14c-4-4-8-2-8-2s2 5 8 4M20 12c4-4 8-2 8-2s-2 5-8 4M20 22l-4 6M20 22l4 6"/></svg></div>
    <div class="fix-label" style="top:488px">ROOT<br>INTRUSION</div>
    <div class="tile" style="left:49px;top:555px"><svg viewBox="0 0 40 40"><path d="M6 30V14a6 6 0 0 1 6-6h20M32 5v6"/><path d="M14 20v2M20 24v2"/><path d="M12 36l22-12-3-4-3 2"/></svg></div>
    <div class="fix-label" style="top:558px">RECURRING<br>PLUMBING<br>PROBLEMS</div>
  </section>

</div>
</body>
</html>
```